KVR Inc Web Design

WHAT ARE WE DOING?
We are developing a new website look and feel for a new company called KVR Inc. This new look and feel should include colors, design elements, choice of photography and other imagery, fonts, and other user experience elements.

WHAT DO THEY DO?
KVR, Inc, makes tools for researchers who are studying protein-protein interactions. These molecules are the basic tools of biology, and serve as key targets for drug developers and disease researchers. The world of proteins is enormously complex, and companies like KVR provide researchers with critical tools that help them elucidate this world.

WHO ARE WE TALKING TO?
The target audience for this website are professional scientists working in university research or biopharma drug development. They are highly sophisticated consumers looking for key tools that will advance their research.

WHAT DO WE WANT THEM TO DO?
The site is an information resource for the customer exploring the tools that KVR sells and the scientific issues surrounding protein-protein interactions. They should be able to navigate easily to their content of choice, while the whole site should convey a professionalism that enhanced KVR’s credibility.

WHAT DOES THE KVR BRAND STAND FOR?
KVR stands for illumination. Proteins are challenging to study, and KVR exists to help shed light on their workings.

WHAT ARE THE KEY VALUES OF THE KVR BRAND?
Integrity. Innovation. Insight.

WHAT ARE THE EXECUTIONAL MANDITORIES?
The look and feel is completely up for grabs. Nothing is off the table.

WHAT ARE THE DELIVERABLES?
We need new designs for the following templates:
http://cms.marlowbench.com/
http://cms.marlowbench.com/products-and-services/instruments-3/bench-top-instruments/
http://cms.marlowbench.com/category/lab-study/

```html
<!DOCTYPE html>
<html lang="en">
<head>
<meta charset="utf-8">
<title>KVR Inc – Featured Report</title>
<link rel="stylesheet" href="https://fonts.googleapis.com/css2?family=Ubuntu:wght@300;400;500&display=swap">
<style>
:root{
  --blue:#35b0d6;
  --orange:#fbb03b;
  --text:#555;
  --dark:#222;
  --grey-panel:#b3b3b3;
  --grey-tag:#a8a8a8;
  --line:#d9d9d9;
  --footer:#6b6b6b;
}
*{box-sizing:border-box;margin:0;padding:0}
html,body{width:1092px;height:1200px;overflow:hidden;background:#fff}
body{font-family:"Ubuntu",sans-serif;color:var(--text)}
.page{width:1280px;height:1406px;position:relative;transform:scale(0.853125);transform-origin:0 0;border-top:3px solid var(--orange)}
a{text-decoration:none;color:inherit}

.site-header{height:62px;border-bottom:1px solid #e6e6e6;position:relative}
.brand{position:absolute;left:128px;top:12px;font-size:32px;font-weight:400;letter-spacing:8px;color:#666}
.main-nav{position:absolute;left:326px;top:19px;display:flex;gap:24px;font-size:17px;font-weight:500;color:#666}
.main-nav .active{color:var(--orange)}
.site-search{position:absolute;left:1005px;top:17px;width:147px;height:26px;background:linear-gradient(#8f8f8f,#a5a5a5);color:#eee;font-size:14px;padding:5px 8px}
.site-search svg{position:absolute;right:7px;top:6px}

.featured{position:absolute;left:128px;top:97px;width:1024px}
.featured h1{font-size:30px;font-weight:400;color:var(--dark);padding-bottom:8px;border-bottom:3px double #ccc}
.featured-title{margin-top:26px;font-size:22px;color:var(--dark);font-weight:400}
.featured-title a{color:var(--orange);font-size:20px;margin-left:22px}

.filter-bar{position:absolute;left:127px;top:209px;width:1025px;height:62px;background:var(--grey-panel)}
.field{position:absolute;top:18px;height:27px;background:#fff;color:#aaa;font-size:14px;padding:6px 16px}
.field svg{position:absolute;right:14px;top:10px}
.btn-search{position:absolute;left:865px;top:18px;width:135px;height:27px;background:var(--orange);color:#fff;font-size:15px;font-weight:500;text-align:center;line-height:27px}

.sidebar{position:absolute;left:128px;top:308px;width:235px;height:794px;background:#fff;box-shadow:0 1px 3px rgba(0,0,0,.35)}
.sidebar h2{background:var(--blue);color:#fff;font-size:19px;font-weight:500;height:43px;line-height:43px;padding-left:19px}
.side-list{list-style:none;margin-top:8px}
.side-list li{height:36px;line-height:36px;border-bottom:1px solid #e2e2e2;padding-left:20px;font-size:17px;color:#666}
.side-list li:last-child{border-bottom:none}
.side-list li::before{content:"»";font-size:13px;margin-right:6px;position:relative;top:-2px}
.side-list li.current{background:#aaa;color:#fff}
.promo-head{margin-top:14px;background:var(--blue);color:#fff;font-size:19px;font-weight:500;line-height:20px;padding:11px 19px 11px;height:63px}
.promo-img{margin:14px 0 0 17px;width:202px;height:202px;background:linear-gradient(135deg,#cfdde6,#f4f6f8 50%,#b8c8d4)}
.promo-text{margin:12px 16px 0;font-size:14px;line-height:18px;color:#555}
.btn-click{display:block;margin:13px 0 0 16px;width:135px;height:27px;line-height:27px;text-align:center;background:var(--orange);color:#fff;font-size:15px}

.order-bar{position:absolute;left:389px;top:308px;display:flex;align-items:center;font-size:14px;color:var(--orange)}
.order-tag{background:var(--grey-tag);color:#fff;height:28px;line-height:28px;padding:0 15px;position:relative;margin-right:32px}
.order-tag::after{content:"";position:absolute;right:-10px;top:0;border-left:10px solid var(--grey-tag);border-top:14px solid transparent;border-bottom:14px solid transparent}
.order-bar .sep{margin:0 10px}
.order-bar .dir{display:inline-flex;align-items:center;gap:3px;margin-left:18px}

.results{position:absolute;left:390px;top:356px;display:grid;grid-template-columns:repeat(3,237px);column-gap:26px;grid-template-rows:318px 321px auto}
.card-media{width:237px;height:184px;border:1px solid #ddd;padding:6px}
.card-media div{width:100%;height:100%}
.card h3{margin-top:18px;font-size:15.5px;font-weight:500;color:var(--blue);line-height:19px}
.card p{margin-top:4px;font-size:13.5px;line-height:18px;color:#555}
.card .more{display:block;margin-top:3px;font-size:13.5px;color:var(--orange)}
.img-lab{background:linear-gradient(135deg,#eef2f5,#c9d6e2 45%,#5a86b8 75%,#dfe7ee)}
.img-team{background:linear-gradient(120deg,#dfe6ea,#f3efe9 45%,#c6d3de 70%,#eaeef1)}
.img-plate{background:linear-gradient(#2a8fd6,#5ec2ea 55%,#1e7fc7)}
.img-animal{background:radial-gradient(ellipse at 50% 55%,#8a8582 0,#b9b3ae 30%,#fff 62%)}
.img-bench{background:linear-gradient(135deg,#dbe6ef,#a9c3da 50%,#eef3f7)}
.img-group{background:linear-gradient(120deg,#eceae6,#d8d2ca 45%,#f5f5f4 75%,#cfd9e1)}

.site-footer{position:absolute;left:0;top:1339px;width:1280px;height:67px;background:var(--footer);color:#fff}
.foot-nav{position:absolute;left:128px;top:27px;font-size:14px}
.foot-nav span{margin:0 6px}
.social{position:absolute;left:879px;top:23px;display:flex;gap:5px}
.social i{display:block;width:26px;height:26px;border-radius:50%;background:#fff}
.copyright{position:absolute;left:991px;top:28px;font-size:15px}
.copyright em{font-style:normal;color:var(--orange)}
</style>
</head>
<body>
<div class="page">
  <header class="site-header">
    <a class="brand" href="#">KVR INC</a>
    <nav class="main-nav">
      <a href="#">Company</a><a class="active" href="#">Products &amp; Services</a><a href="#">Learning Center</a><a href="#">Events</a><a href="#">KVR News</a><a href="#">Contact</a>
    </nav>
    <div class="site-search">Search
      <svg width="14" height="14" viewBox="0 0 14 14"><circle cx="6" cy="6" r="4.5" fill="none" stroke="#ccc" stroke-width="1.6"/><line x1="9.3" y1="9.3" x2="13" y2="13" stroke="#ccc" stroke-width="1.8"/></svg>
    </div>
  </header>

  <section class="featured">
    <h1>FEATURED REPORT</h1>
    <p class="featured-title">Screening assays for GPCR ligands 3 <a href="#">Read &amp; Download ➔</a></p>
  </section>

  <form class="filter-bar">
    <div class="field" style="left:23px;width:277px">Keyword</div>
    <div class="field" style="left:311px;width:257px">Topic<svg width="14" height="8"><path d="M0 0h14L7 8z" fill="#999"/></svg></div>
    <div class="field" style="left:580px;width:267px">Media Types<svg width="14" height="8"><path d="M0 0h14L7 8z" fill="#999"/></svg></div>
    <div class="btn-search"><svg width="12" height="12" viewBox="0 0 14 14"><circle cx="6" cy="6" r="4.5" fill="none" stroke="#fff" stroke-width="2"/><line x1="9.3" y1="9.3" x2="13" y2="13" stroke="#fff" stroke-width="2.2"/></svg> Search Now</div>
  </form>

  <aside class="sidebar">
    <h2>Overview</h2>
    <ul class="side-list">
      <li>Application Note</li><li class="current">Manual</li><li>PDF’s</li><li>Report</li><li>White Paper</li><li>Pipette Calibration</li><li>Application Note</li><li>Common Errors</li>
    </ul>
    <div class="promo-head">Ready to save time<br>in your lab?</div>
    <div class="promo-img" role="img" aria-label="Automated lab instrument with orange accents"></div>
    <p class="promo-text">to have a member of our team Demo what KVR’s instruments could do for you.</p>
    <a class="btn-click" href="#">Click Here</a>
  </aside>

  <div class="order-bar">
    <span class="order-tag">Order by</span>
    DATE<span class="sep">|</span>TITLE
    <span class="dir">ASCENDING<svg width="12" height="7"><path d="M0 0h12L6 7z" fill="#fbb03b"/></svg></span>
    <span class="dir" style="margin-left:36px">DESCENDING<svg width="12" height="7"><path d="M0 7h12L6 0z" fill="#fbb03b"/></svg></span>
  </div>

  <main class="results">
    <article class="card"><div class="card-media"><div class="img-lab" role="img" aria-label="Scientist at a microscope in a lab"></div></div>
      <h3>Sample Prep Checklist</h3><p>Dr. Thomas Hale, Aug 2013<br>Application Note, Manual</p><a class="more" href="#">Read More ➔</a></article>
    <article class="card"><div class="card-media"><div class="img-team" role="img" aria-label="Lab researchers working at a bench"></div></div>
      <h3>Screening Assays for GPCR...</h3><p>Dr. Helen Marsh, Aug 2013<br>Application Note, Video</p><a class="more" href="#">Read More ➔</a></article>
    <article class="card"><div class="card-media"><div class="img-plate" role="img" aria-label="Pipette tips over a blue well plate"></div></div>
      <h3>Lorem ipsum dolor sit amet, consectetur adipiscing elit</h3><p>Northfield University, July 2013<br>Manual, Report</p><a class="more" href="#">Read More ➔</a></article>

    <article class="card"><div class="card-media"><div class="img-animal" role="img" aria-label="Grey lab mouse on white"></div></div>
      <h3>Nam venenatis nisl libero</h3><p>Northfield University, July 2013<br>Manual, Report</p><a class="more" href="#">Read More ➔</a></article>
    <article class="card"><div class="card-media"><div class="img-bench" role="img" aria-label="Researchers examining a plant sample"></div></div>
      <h3>Duis aliquam purus sed nulla faucibus</h3><p>Paul Devereux PHD</p><a class="more" href="#">Read More ➔</a></article>
    <article class="card"><div class="card-media"><div class="img-bench" role="img" aria-label="Researchers examining a plant sample"></div></div>
      <h3>Sample Prep Checklist</h3><p>Dr. Thomas Hale, Aug 2013<br>Application Note, Manual</p><a class="more" href="#">Read More ➔</a></article>

    <article class="card"><div class="card-media"><div class="img-lab" role="img" aria-label="Scientist at a microscope in a lab"></div></div>
      <h3>Lorem ipsum dolor sit amet nisl consectetur adipiscing elit</h3><p>Dr. Thomas Hale, Aug 2013<br>&nbsp;PDF, White Paper</p><a class="more" href="#">Read More ➔</a></article>
    <article class="card"><div class="card-media"><div class="img-team" role="img" aria-label="Lab researchers working at a bench"></div></div>
      <h3>Screening Assays for GPCR...</h3><p>Dr. Thomas Hale, Aug 2013<br>Application Note, Manual</p><a class="more" href="#">Read More ➔</a></article>
    <article class="card"><div class="card-media"><div class="img-group" role="img" aria-label="Group of scientists in safety glasses"></div></div>
      <h3>Nam venenatis nisl libero</h3><p>Dr. Thomas Hale, Aug 2013<br>Application Note, Manual</p><a class="more" href="#">Read More ➔</a></article>
  </main>

  <footer class="site-footer">
    <nav class="foot-nav">Company<span>-</span>Products &amp; Services<span>-</span>Learning Center<span>-</span>Events<span>-</span>KVR News<span>-</span>Contact</nav>
    <div class="social"><i></i><i></i><i></i></div>
    <p class="copyright">Copyright © <em>KVR Inc.</em> 2013</p>
  </footer>
</div>
</body>
</html>
```